Etiketten-Design für Honiggläser
Zielgruppe
kleine Hobby-Imkerei, Zielgruppe 'Regionale Käufer', die gerne Wissen, wo ihr Honig her kommt. Mittleres Preissegment
Aufgabenstellung
Das Etikett soll für meine Honiggläser dienen. Die Maße sind 134 x 64 mm. Die Breite kann bis 150 mm variieren, die Höhe nicht.
Pflichtangaben : 'Deutscher xxx Honig (z.B. Blütenhonig), Name und Anschrift (Matthias Kehl Birkenweg 12 73912 Ludwigsburg M.Kehl@postfeld.de), mindestens haltbar bis(wird gestempelt, Fläche min. 30x7mm, Gewicht 500 g(Schriftgröße min. 4 mm), 'Mehrwegglas'. Schriftgröße mindestens 1,2mm bezogen auf das kleine „x“. Optional Lagerbedingungen, s. bisheriges Etikett.
Das angehängte Bild soll in irgendeiner Form mit eingebunden wäre, gerne können Farben und Form aber verändert werden, Bildrechte sind bei mir. Anbei auch mein bisheriges, selber entworfenes Etikett.
Das neue Etikett soll moderner und ansprechender werden, der Regionalitätsbezug etwas besser herausgearbeitet werden. Gelb hat sich als Farbe nicht bewährt, da das gelb des Honig sich manchmal beißt.

```html
<!DOCTYPE html>
<html lang="de">
<head>
<meta charset="utf-8">
<title>Deutscher Blütenhonig – Etikett</title>
<link rel="stylesheet" href="https://fonts.googleapis.com/css2?family=Arimo:ital,wght@0,400;0,700;1,700&family=Pangolin&display=swap">
<style>
  :root {
    --panel: #f4f1e8;
    --panel-low: #e6ebdf;
    --forest: #2f5b3a;
    --forest-deep: #234530;
    --sky: #b9d3e6;
    --meadow: #6fa84a;
    --hex-fill: #fbfaf5;
    --hex-line: #2f5b3a;
    --accent: #b5452e;
    --ink: #24302a;
    --white: #ffffff;
    --placeholder: #c9d4c3;
  }
  html, body {
    margin: 0;
    padding: 0;
    width: 1200px;
    height: 581px;
    overflow: hidden;
    background: #ffffff;
  }
  .label {
    position: relative;
    width: 1200px;
    height: 581px;
    overflow: hidden;
    font-family: "Arimo", Arial, sans-serif;
    color: var(--ink);
  }
  .side-panel {
    position: absolute;
    top: 0;
    height: 581px;
    background: linear-gradient(180deg, var(--panel) 0%, var(--panel) 45%, var(--panel-low) 100%);
  }
  .side-panel--left { left: 0; width: 256px; }
  .side-panel--right { left: 944px; width: 256px; }
  .scene {
    position: absolute;
    left: 256px;
    top: 0;
    width: 688px;
    height: 502px;
    background: linear-gradient(180deg, var(--sky) 0%, #dce6ea 32%, #c9dba8 44%, #8dbd5c 54%, var(--meadow) 76%, #4a8236 100%);
  }
  .bottom-band {
    position: absolute;
    left: 256px;
    top: 502px;
    width: 688px;
    height: 79px;
    background: var(--forest);
  }
  .product-badge {
    position: absolute;
    left: 466px;
    top: 12px;
    width: 268px;
    height: 296px;
  }
  .product-name {
    position: absolute;
    left: 466px;
    width: 268px;
    text-align: center;
    font-family: "Pangolin", "Comic Sans MS", cursive;
    color: var(--accent);
    line-height: 1;
    margin: 0;
  }
  .product-name--kind { top: 140px; font-size: 33px; }
  .product-name--type { top: 182px; font-size: 33px; }
  .product-name--weight { top: 226px; font-size: 36px; }
  .apiary-claim {
    position: absolute;
    left: 0;
    top: 120px;
    width: 256px;
    margin: 0;
    text-align: center;
    color: var(--forest);
    font-size: 30px;
    line-height: 44px;
  }
  .address {
    position: absolute;
    left: 0;
    top: 244px;
    width: 256px;
    margin: 0;
    text-align: center;
    font-style: normal;
    font-size: 19px;
    line-height: 27px;
  }
  .best-before-label {
    position: absolute;
    left: 35px;
    top: 482px;
    margin: 0;
    font-size: 15px;
  }
  .best-before-field {
    position: absolute;
    left: 35px;
    top: 505px;
    width: 268px;
    height: 63px;
    background: var(--white);
    border: 1px solid #c4cbbd;
    box-sizing: border-box;
  }
  .storage {
    position: absolute;
    left: 944px;
    top: 124px;
    width: 256px;
    margin: 0;
    text-align: center;
    font-size: 22px;
    line-height: 29px;
  }
  .liquefy-note {
    position: absolute;
    left: 956px;
    top: 244px;
    width: 240px;
    margin: 0;
    font-size: 19px;
    line-height: 27px;
  }
  .origin {
    position: absolute;
    left: 256px;
    top: 519px;
    width: 688px;
    margin: 0;
    text-align: center;
    font-size: 27px;
    color: var(--white);
  }
  .returnable {
    position: absolute;
    left: 956px;
    top: 516px;
    margin: 0;
    font-size: 17px;
    font-weight: 700;
    font-style: italic;
    color: var(--forest-deep);
  }
</style>
</head>
<body>
<main class="label">
  <div class="side-panel side-panel--left"></div>
  <div class="side-panel side-panel--right"></div>
  <div class="scene" role="img" aria-label="Gemalte Frühlingslandschaft mit blühenden Bäumen, Wiese und vier weißen Bienenstöcken"></div>
  <div class="bottom-band"></div>

  <svg class="product-badge" viewBox="0 0 268 296" aria-hidden="true">
    <polygon points="134,4 262,78 262,226 134,292 6,226 6,78" fill="var(--hex-fill)" stroke="var(--hex-line)" stroke-width="4"/>
    <rect x="104" y="16" width="60" height="94" rx="20" fill="var(--placeholder)"/>
  </svg>
  <div role="img" aria-label="Gezeichnete Biene mit Honiglöffel" style="position:absolute;left:570px;top:28px;width:60px;height:94px;"></div>
  <p class="product-name product-name--kind">Deutscher</p>
  <p class="product-name product-name--type">Blütenhonig</p>
  <p class="product-name product-name--weight">500g</p>

  <p class="apiary-claim">Aus eigener<br>Imkerei</p>
  <address class="address">Matthias Kehl<br>Birkenweg 12<br>73912 Ludwigsburg<br>M.Kehl@postfeld.de</address>
  <p class="best-before-label">Mindsthaltbar bis</p>
  <div class="best-before-field"></div>

  <p class="storage">Trocken, kühl und<br>dunkel lagern</p>
  <p class="liquefy-note">Honig kann fest<br>werden. Sie können<br>kristalisierten Honig<br>im Wasswebad<br>(bis 40 ) wieder<br>verflüssigen.</p>

  <p class="origin">100 % Honig aus Ludwigsburg</p>
  <p class="returnable">Mehrwegglas</p>
</main>
</body>
</html>
```